Wordpress Site Design for a Horror and Action Movie Production Company

We need a re-design/facelift of our website: https://k42t.pagecraft.io
The structure of the website could remain the same, but it needs to look and feel BETTER!

We would like the website coded in Wordpress so that it can be easily updated bu us, via adding new projects and new projects' info.

We specialize in Action, Horror, and Sci-Fi Genre. That being said, we don't want the website to look like it's a themed park with haunted houses. It should still be sharp and professional, as after all - it is a business for us!

Target Market(s)

Film Distribution Companies (B2B), as well as general audience that likes movies

Industry/Entity Type

Movie Production

Coding

Coded - Design and coding required

Number of Pages Required

5+ page

Font styles to use
Sans Serif

Colors

Designer to choose colors to be used in the design.

Requirements
Must have
• - PROJECTS page
• - Each PROJECT has a sub-page with project info/updates (up dates could be in a form of a WP post, ideally a template that we can use to update and create new PROJECT pages, with text, poster, and video link (trailer))
• - NEWS page that chronologically lists updates from all PROJECTS (could be done via WP blog)
• - HOME page would
Nice to have
• Should generally have a dark background.
• Websites we like as a reference of general approach and style:
• https://marbletoq.com
• https://velunpix.com (however this is very image-centric, and we might not have that much imagery at the moment)
• https://www.copperfieldechoandframe.com/other
• https://quennreels.com
Should not have
• We specialize in Action, Horror, and Sci-Fi Genre. That being said, we don't want the website to look like it's a themed park with haunted houses. It should still be sharp and professional, as after all - it is a business for us!

```html
<!DOCTYPE html>
<html lang="en">
<head>
<meta charset="utf-8">
<title>Kestrel 42 Media — Movie Production Company</title>
<link rel="stylesheet" href="https://fonts.googleapis.com/css2?family=Montserrat:wght@400;500;600;700&family=Oswald:wght@400;500&display=swap">
<style>
:root{
  --red:#d6111b;
  --ink:#1b1c1e;
  --ink-3:#2b2d31;
  --white:#ffffff;
  --grey:#c9cbd0;
  --card-text:#3a3a3a;
}
*{box-sizing:border-box;margin:0;padding:0}
html,body{width:1200px;height:3479px;overflow:hidden;background:var(--ink)}
body{font-family:'Montserrat',sans-serif;color:var(--white);position:relative}
section,header,footer{position:absolute;left:0;width:1200px}
.abs{position:absolute}
.btn{position:absolute;background:var(--red);color:var(--white);font:700 13px 'Montserrat',sans-serif;letter-spacing:.5px;display:flex;align-items:center;justify-content:center;text-transform:uppercase}
.section-title{position:absolute;left:0;width:1200px;text-align:center;font:700 30px 'Montserrat',sans-serif;letter-spacing:3px;text-transform:uppercase}
.title-rule{position:absolute;left:565px;width:70px;height:2px;background:var(--grey)}

/* brand name */
.brand{position:absolute;white-space:nowrap;font:600 22px 'Montserrat',sans-serif;letter-spacing:1.5px;color:var(--white)}

/* hero */
.hero{top:0;height:620px;background:radial-gradient(ellipse at 55% 45%,#6e7a86 0%,#3d4852 40%,#1f262d 80%);overflow:hidden}
.hero .brand{left:142px;top:56px}
.main-nav{position:absolute;top:64px;left:589px;display:flex}
.main-nav a{color:var(--white);text-decoration:none;font:500 15px 'Montserrat',sans-serif;margin-right:46px;position:relative}
.main-nav a.active{font-weight:700}
.main-nav a.active::before{content:"";position:absolute;left:-4px;right:-4px;top:-9px;height:2px;border-top:2px solid var(--white);border-radius:50% 50% 0 0}
.hero-photo{position:absolute;left:380px;top:230px;width:420px;height:330px;background:radial-gradient(ellipse,#3a3f45 0%,rgba(40,45,50,0) 70%)}
.hero h1{position:absolute;top:232px;left:0;width:1200px;text-align:center;font:500 37px 'Oswald',sans-serif;letter-spacing:.3px}
.hero h2{position:absolute;top:282px;left:0;width:1200px;text-align:center;font:400 28px 'Oswald',sans-serif}
.hero-curve{position:absolute;left:0;top:540px}

/* about */
.about{top:620px;height:548px;background:linear-gradient(180deg,#1b1c1e 0%,#222326 100%)}
.about-kicker{position:absolute;top:16px;left:0;width:1200px;text-align:center;font:400 23px 'Montserrat',sans-serif;letter-spacing:2px}
.about-title{position:absolute;top:46px;left:0;width:1200px;text-align:center;font:700 28px 'Montserrat',sans-serif;letter-spacing:2px}
.about-copy{position:absolute;top:118px;left:146px;width:910px;font:400 12.5px/23px 'Montserrat',sans-serif;color:var(--grey);text-align:center}
.about-copy p{margin-bottom:14px}
.partner{position:absolute;top:330px;width:440px}
.partner-mark{position:absolute;top:2px;background:var(--grey);opacity:.85}
.partner h3{position:absolute;left:68px;top:0;font:600 18px 'Montserrat',sans-serif;white-space:nowrap}
.partner p{position:absolute;left:68px;top:28px;width:340px;font:400 12px/19px 'Montserrat',sans-serif;color:var(--grey)}

/* specialties */
.specialties{top:1168px;height:632px;background:linear-gradient(135deg,#3a302a 0%,#2a2420 45%,#1c1a19 100%)}
.spec-card{position:absolute;top:186px;width:239px;height:293px;background:var(--white);border-radius:4px;overflow:hidden}
.spec-photo{position:absolute;left:4px;top:4px;width:231px;height:156px}
.spec-card svg.curve{position:absolute;left:0;top:132px}
.spec-badge{position:absolute;left:100px;top:131px;width:40px;height:40px;border-radius:50%;background:var(--white);border:2px solid #f2c9cb}
.spec-badge::after{content:"";position:absolute;left:11px;top:11px;width:14px;height:14px;border:2px solid var(--red);border-radius:50%}
.spec-card h3{position:absolute;top:182px;left:0;width:100%;text-align:center;font:600 16px 'Montserrat',sans-serif;color:#111;letter-spacing:.5px}
.spec-card p{position:absolute;top:210px;left:24px;width:191px;text-align:center;font:400 12px/19px 'Montserrat',sans-serif;color:var(--card-text)}

/* projects */
.projects{top:1800px;height:728px;background:var(--ink)}
.tile{position:absolute;width:293px;height:247px}
.tile-hover{position:absolute;left:16px;top:14px;width:262px;height:220px;background:rgba(214,17,27,.92)}
.tile-hover h4{position:absolute;top:52px;left:0;width:100%;text-align:center;font:600 16px 'Montserrat',sans-serif}
.tile-hover p{position:absolute;top:86px;left:20px;width:222px;text-align:center;font:400 12px/16px 'Montserrat',sans-serif;color:#f4c7c9}
.tile-hover svg{position:absolute;left:112px;top:142px}

/* news */
.news{top:2528px;height:584px;background:linear-gradient(180deg,#26272a 0%,#1d1e21 60%,#19191b 100%)}
.news-card{position:absolute;top:156px;width:220px;height:289px;background:var(--white);border-radius:3px;overflow:hidden}
.news-photo{position:absolute;left:4px;top:4px;width:212px;height:150px}
.news-card h4{position:absolute;top:180px;left:12px;width:196px;text-align:center;font:600 12.5px/20px 'Montserrat',sans-serif;color:#151515}
.news-card a{position:absolute;top:257px;left:0;width:100%;text-align:center;font:600 11px 'Montserrat',sans-serif;color:#444;text-decoration:none;letter-spacing:.5px}
.news-card a.hot{color:var(--red)}

/* footer */
.site-footer{top:3112px;height:367px;background:var(--ink-3)}
.site-footer .brand{left:0;width:1200px;text-align:center;top:64px}
.foot-nav{position:absolute;top:151px;left:0;width:1200px;font:500 12px 'Montserrat',sans-serif}
.foot-nav span{position:absolute}
.contact-item{position:absolute;top:195px;width:200px;text-align:center;font:400 12px/15px 'Montserrat',sans-serif}
.contact-item .dot{display:block;margin:0 auto 14px;width:30px;height:30px;border-radius:50%;background:var(--red);position:relative}
.contact-item .dot svg{position:absolute;left:7px;top:7px}
.copyright{position:absolute;top:328px;left:0;width:1200px;height:39px;background:#19191b;text-align:center;font:500 12px/39px 'Montserrat',sans-serif}
</style>
</head>
<body>

<section class="hero">
  <div class="hero-photo" role="img" aria-label="Misty horror scene of a figure crawling through fog"></div>
  <div class="brand">KESTREL 42 MEDIA</div>
  <nav class="main-nav">
    <a class="active">HOME</a><a>ABOUT</a><a>NEWS</a><a>PROJECT</a><a>CONTACT</a>
  </nav>
  <h1>WE ARE A MOVIE PRODUCTION COMPANY</h1>
  <h2>SPECIALIZING IN ACTION, HORROR AND SCI-FI GENRE MOVIES</h2>
  <div class="btn" style="left:513px;top:337px;width:175px;height:31px">Contact Us Today</div>
  <svg class="hero-curve" width="1200" height="80" viewBox="0 0 1200 80">
    <path d="M0 80 L0 78 Q600 -40 1200 78 L1200 80 Z" fill="#1b1c1e"/>
    <path d="M0 78 Q600 -40 1200 78 L1200 64 Q600 -20 0 78 Z" fill="var(--red)"/>
    <path d="M0 80 Q600 -12 1200 70 L1200 80 Z" fill="#1b1c1e"/>
  </svg>
</section>

<section class="about">
  <div class="about-kicker">ABOUT</div>
  <div class="about-title">KESTREL 42 MEDIA</div>
  <div class="title-rule" style="top:98px"></div>
  <div class="about-copy">
    <p>Kestrel 42 Media is a fresh brand of multi-media entertainment, aimed at development of original Canadian content as well as<br>servicing of foreign productions in Toronto, Ontario, Canada.</p>
    <p>We produce genre feature films, series, documentaries, and anything else that we feel great about. We take pride in our innovative approach<br>to the process of filmmaking and marketing of our produced content. In simple terms, we make good looking motion picture content that is<br>entertaining, visually compelling, and tells a good story.</p>
    <p>K42M is a child of a partnership between two Canadian companies, which for years have been recognized<br>as key brands in the Canadian media landscape:</p>
  </div>
  <div class="partner" style="left:142px">
    <div class="partner-mark" style="border-radius:50%;width:32px;height:32px;left:12px"></div>
    <h3>Corvid Flag Entertainment Inc</h3>
    <p>Corvid Flag Entertainment is led by partners Marcus Dovel, Adrian Holt and Jonas Frey. It represents unique...(+)</p>
  </div>
  <div class="partner" style="left:610px">
    <div class="partner-mark" style="width:30px;height:30px;left:14px"></div>
    <h3>Seven Lantern Entertainment Inc</h3>
    <p>Seven Lantern Entertainment is founded by Pavel Tarkin csc in 2015, and has since quickly gained momentum. It has been the name...(+)</p>
  </div>
  <div class="btn" style="left:529px;top:422px;width:141px;height:33px">Read More</div>
</section>

<section class="specialties" role="img" aria-label="Dark ruined city backdrop with rocky cliffs">
  <div class="section-title" style="top:96px">We Specialized In</div>
  <div class="title-rule" style="top:142px"></div>

  <div class="spec-card" style="left:142px">
    <div class="spec-photo" role="img" aria-label="Action film still with armed soldiers" style="background:linear-gradient(160deg,#7a7f82,#3c3e3a)"></div>
    <svg class="curve" width="239" height="40"><path d="M0 30 Q120 -6 239 30 L239 40 L0 40Z" fill="#fff"/><path d="M0 30 Q120 -6 239 30" stroke="var(--red)" stroke-width="4" fill="none"/></svg>
    <div class="spec-badge"></div>
    <h3>ACTION</h3>
    <p>Lorem ipsum dolor sit amet consectetuer adipiscing elit, sed diam nonummy nibh eui.</p>
  </div>
  <div class="spec-card" style="left:481px">
    <div class="spec-photo" role="img" aria-label="Horror film still of a scarecrow in a dark field" style="background:linear-gradient(160deg,#3e4a48,#1f2623)"></div>
    <svg class="curve" width="239" height="40"><path d="M0 30 Q120 -6 239 30 L239 40 L0 40Z" fill="#fff"/><path d="M0 30 Q120 -6 239 30" stroke="var(--red)" stroke-width="4" fill="none"/></svg>
    <div class="spec-badge"></div>
    <h3>HORROR</h3>
    <p>Lorem ipsum dolor sit amet consectetuer adipiscing elit, sed diam nonummy nibh eui.</p>
  </div>
  <div class="spec-card" style="left:820px">
    <div class="spec-photo" role="img" aria-label="Sci-fi film still with glowing visor" style="background:linear-gradient(160deg,#6a5b86,#2f3346 60%,#a0434d)"></div>
    <svg class="curve" width="239" height="40"><path d="M0 30 Q120 -6 239 30 L239 40 L0 40Z" fill="#fff"/><path d="M0 30 Q120 -6 239 30" stroke="var(--red)" stroke-width="4" fill="none"/></svg>
    <div class="spec-badge"></div>
    <h3>SCI-FI GENRE MOVIES</h3>
    <p>Lorem ipsum dolor sit amet consectetuer adipiscing elit, sed diam nonummy nibh eui.</p>
  </div>

  <svg class="abs" style="left:250px;top:467px" width="24" height="24"><circle cx="12" cy="12" r="11" fill="#2a2a2a" stroke="#fff" stroke-width="1.5"/><path d="M12 6v12M6 12h12" stroke="#fff" stroke-width="2"/></svg>
  <svg class="abs" style="left:589px;top:467px" width="24" height="24"><circle cx="12" cy="12" r="11" fill="#2a2a2a" stroke="#fff" stroke-width="1.5"/><path d="M12 6v12M6 12h12" stroke="#fff" stroke-width="2"/></svg>
  <svg class="abs" style="left:928px;top:467px" width="24" height="24"><circle cx="12" cy="12" r="11" fill="#2a2a2a" stroke="#fff" stroke-width="1.5"/><path d="M12 6v12M6 12h12" stroke="#fff" stroke-width="2"/></svg>

  <div class="btn" style="left:513px;top:530px;width:175px;height:31px">Contact Us Today</div>
</section>

<section class="projects">
  <div class="section-title" style="top:70px">Our Projects</div>
  <div class="title-rule" style="top:120px"></div>

  <div class="tile" style="left:0;top:158px;background:linear-gradient(135deg,#9a8e88,#3a2f31 70%,#7a1a20)" role="img" aria-label="Film poster with tattooed hands covering a face"></div>
  <div class="tile" style="left:302px;top:158px;background:linear-gradient(135deg,#5a5a5a,#2b2b2b)" role="img" aria-label="Film poster with a mechanical wheel">
    <div class="tile-hover">
      <h4>Lorem Ipsum Dolar</h4>
      <p>Lorem ipsum dolor sit amet elit consectetuer adipiscing</p>
      <svg width="38" height="38" viewBox="0 0 38 38"><circle cx="15" cy="15" r="11" stroke="#fff" stroke-width="3" fill="none"/><path d="M23 23l11 11" stroke="#fff" stroke-width="4" stroke-linecap="round"/><path d="M15 9v12M9 15h12" stroke="#fff" stroke-width="2.5"/></svg>
    </div>
  </div>
  <div class="tile" style="left:604px;top:158px;background:linear-gradient(135deg,#4a3a30,#241b17)" role="img" aria-label="Film still of a bearded man in low light"></div>
  <div class="tile" style="left:906px;top:158px;background:linear-gradient(135deg,#5a6168,#2a2f34 60%,#6a2a22)" role="img" aria-label="Action film poster with two armed men"></div>

  <div class="tile" style="left:0;top:411px;background:linear-gradient(135deg,#c8b8a4,#7a2a22 50%,#2a1a18)" role="img" aria-label="Film poster with a woman and red splatter"></div>
  <div class="tile" style="left:302px;top:411px;background:linear-gradient(135deg,#6d7f96,#3c4758 55%,#b4602a)" role="img" aria-label="Sci-fi film poster with a battle scene and explosions"></div>
  <div class="tile" style="left:604px;top:411px;background:linear-gradient(135deg,#3a3430,#1c1817)" role="img" aria-label="Film still of a boxer in a dark gym"></div>
  <div class="tile" style="left:906px;top:411px;background:linear-gradient(135deg,#7a7c80,#2a2c30)" role="img" aria-label="Sci-fi film poster with a planet"></div>
</section>

<section class="news" role="img" aria-label="Dark gothic backdrop with bare trees">
  <div class="section-title" style="top:74px">Latest News</div>
  <div class="title-rule" style="top:120px"></div>

  <div class="news-card" style="left:142px">
    <div class="news-photo" role="img" aria-label="Press photo of a man in a suit" style="background:linear-gradient(160deg,#6a4a3a,#2a1e1a)"></div>
    <h4>Reel Weekly: Corvid Flag partners on production arm, Kestrel 42 Media</h4>
    <a>READ MORE</a>
  </div>
  <div class="news-card" style="left:374px">
    <div class="news-photo" role="img" aria-label="Vintage horror film poster artwork" style="background:linear-gradient(160deg,#c22a2a,#4a1010)"></div>
    <h4>FrameDesk Canada: Corvid Flag partners on production arm</h4>
    <a class="hot">READ MORE</a>
  </div>
  <div class="news-card" style="left:606px">
    <div class="news-photo" role="img" aria-label="Cast photo of a group of armed men" style="background:linear-gradient(160deg,#8a8a88,#3a3a38)"></div>
    <h4>Corvid Flag pacts with Seven Lantern, Grey Plaza (Cuebook subscription required)</h4>
    <a>READ MORE</a>
  </div>
  <div class="news-card" style="left:838px">
    <div class="news-photo" role="img" aria-label="Sci-fi film still of a crew on a ship bridge" style="background:linear-gradient(160deg,#4a6a8a,#1e2a3a)"></div>
    <h4 style="font-size:13.5px;line-height:22px">Lorem ipsum vulputate upon velit esse molestie movie consequat eu</h4>
    <a>READ MORE</a>
  </div>

  <div class="btn" style="left:543px;top:481px;width:113px;height:33px">View All</div>
</section>

<footer class="site-footer">
  <div class="brand">KESTREL 42 MEDIA</div>
  <nav class="foot-nav">
    <span style="left:355px">HOME</span><span style="left:455px">ABOUT</span><span style="left:562px">NEWS</span><span style="left:662px">PROJECT</span><span style="left:782px">CONTACT</span>
  </nav>
  <div class="contact-item" style="left:265px">
    <span class="dot"><svg width="16" height="16" viewBox="0 0 16 16"><path d="M8 1a5 5 0 0 0-5 5c0 4 5 9 5 9s5-5 5-9a5 5 0 0 0-5-5z" fill="#fff"/><circle cx="8" cy="6" r="2" fill="var(--red)"/></svg></span>
    22-480 Harbour Rd W., Toronto,<br>ON, M4X 2B7, Canada
  </div>
  <div class="contact-item" style="left:493px">
    <span class="dot"><svg width="16" height="16" viewBox="0 0 16 16"><path d="M3 2l3 0 1 4-2 1c1 2 2 3 4 4l1-2 4 1v3c0 1-1 1-2 1C7 14 2 9 2 4c0-1 0-2 1-2z" fill="#fff"/></svg></span>
    555-014-2290
  </div>
  <div class="contact-item" style="left:722px">
    <span class="dot"><svg width="16" height="16" viewBox="0 0 16 16"><rect x="2" y="4" width="12" height="8" rx="1" fill="#fff"/><path d="M2 4l6 5 6-5" stroke="var(--red)" stroke-width="1.3" fill="none"/></svg></span>
    info@kestrel42media.com
  </div>
  <div class="copyright">Copyright © 2019 KESTREL 42 MEDIA. All Rights Reserved.</div>
</footer>

</body>
</html>
```